Website Redesign project for agency

we're looking to see some new designs for an agency website.
details in this google doc: https://pages.quillmarsh.net/sheet/v/8QrtLm27vXcaPo91HsweKd4Zn0yBuTfg6521-qwLa3c/view?mode=shared
homepage and one inner page/ or the blog page
please visit the google doc above to see the website that needs to be redesigned as well as an example website we like.
if you have any questions please send them to us asap
thank you
Target Market(s)
small business owners
Number of Pages Required
2 page
Font styles to use
Sans Serif
Requirements
Nice to have
- custom design
Should not have
- do not use a template you find online

```html
<!DOCTYPE html>
<html lang="en">
<head>
<meta charset="utf-8">
<title>Web Design Projects – Rise &amp; Reach</title>
<link href="https://fonts.googleapis.com/css2?family=Roboto:wght@400;500;700&display=swap" rel="stylesheet">
<style>
:root{
  --blush:#fdf0f4;
  --mist:#d9e5ec;
  --teal:#3f6e7c;
  --ink:#2f3a3f;
  --rose:#f06d8f;
  --grad-a:#f7719a;
  --grad-b:#c184dc;
  --white:#ffffff;
}
*{box-sizing:border-box;margin:0;padding:0}
html,body{width:1200px;height:3177px;overflow:hidden;background:var(--white);font-family:'Roboto',sans-serif;color:var(--ink)}
.page{position:relative;width:1200px;height:3177px}
.band{position:absolute;left:125px;width:948px;background:var(--blush)}
.band--projects{top:0;height:1317px}
.band--cta{top:1392px;height:851px}
.band--footer{top:2319px;height:858px}

.projects-panel{position:absolute;left:321px;top:41px;width:561px;height:1234px;background:var(--mist);border-radius:34px}
.projects-title{position:absolute;left:0;width:1200px;top:88px;text-align:center;font-weight:700;font-size:28px;letter-spacing:3.2px;color:var(--teal)}
.project{position:absolute;width:415px;height:309px;box-shadow:0 3px 10px rgba(0,0,0,.14);overflow:hidden}
.project--roof{left:157px;top:166px;background:linear-gradient(180deg,#c9d7e3 0%,#b4c3cf 55%,#e3ebf1 100%)}
.project--builder{left:624px;top:166px;background:linear-gradient(180deg,#232a3a 0 10%,#7d8f86 10% 66%,#ffffff 66%)}
.project--kitchen{left:157px;top:521px;background:linear-gradient(180deg,#4b4a4d 0 60%,#ffffff 60%)}
.project--music{left:624px;top:521px;background:linear-gradient(180deg,#ffffff 0 10%,#f3f224 10% 17%,#9aa0b3 17% 70%,#e9e2ee 70%)}
.project--legal{left:157px;top:875px;background:linear-gradient(180deg,#ffffff 0 14%,#5d7a4a 14% 61%,#f6f5f1 61%)}
.project--billing{left:624px;top:875px;background:linear-gradient(180deg,#ffffff 0 10%,#b85a4d 10% 75%,#ffffff 75%)}
.project__hover{position:absolute;inset:0;background:rgba(217,229,236,.55);display:flex;align-items:center;justify-content:center;gap:8px;font-size:17px;font-weight:500;letter-spacing:1.4px;color:var(--ink);padding-bottom:0}
.project__hover svg{width:12px;height:18px}
.carousel-dots{position:absolute;top:1226px;left:570px;display:flex;gap:8px}
.carousel-dots span{width:9px;height:9px;border-radius:50%;background:#b9c3c9}
.carousel-dots span.is-active{background:var(--rose)}

.cta-title{position:absolute;left:0;width:1200px;top:1693px;text-align:center;font-size:42px;font-weight:500;letter-spacing:3.4px;color:var(--teal)}
.cta-sub{position:absolute;left:0;width:1200px;top:1770px;text-align:center;font-size:30px;font-weight:500;letter-spacing:3.6px;line-height:39px;color:var(--rose)}
.cta-button{position:absolute;left:319px;top:1880px;width:559px;height:68px;border-radius:34px;background:linear-gradient(90deg,var(--grad-a),var(--grad-b));box-shadow:0 6px 14px rgba(200,110,160,.3);display:flex;align-items:center;justify-content:center;gap:14px;color:var(--white);font-size:20px;font-weight:700;letter-spacing:7.5px;text-decoration:none}
.cta-button svg{width:10px;height:16px}

.footer-wave{position:absolute;left:125px;top:2825px;width:948px;height:352px}
.footer-col{position:absolute;text-align:center}
.footer-head{font-size:15px;font-weight:700;letter-spacing:2px;color:var(--teal);line-height:26px}
.footer-col--start{left:136px;width:270px;top:2928px}
.footer-col--start p{margin-top:26px;font-size:13.5px;line-height:20px;letter-spacing:.9px;color:var(--ink)}
.footer-phone{margin-top:28px;display:flex;align-items:center;justify-content:center;gap:8px;font-size:16px;letter-spacing:1.2px;color:var(--rose)}
.footer-phone svg{width:17px;height:17px}
.footer-col--brand{left:437px;width:210px;top:2937px}
.brand-name{font-size:24px;font-weight:700;color:var(--ink);letter-spacing:.5px;display:flex;align-items:center;justify-content:center;gap:8px}
.brand-name i{width:10px;height:10px;border-radius:50%;background:var(--teal);display:block}
.footer-col--brand address{margin-top:34px;font-style:normal;font-size:13.5px;line-height:26px;letter-spacing:1px;font-weight:500}
.footer-col--hours{left:669px;width:200px;top:2939px}
.hours{margin-top:44px;font-size:14px;font-weight:500;letter-spacing:1.2px}
.pill{position:absolute;height:40px;border-radius:20px;background:linear-gradient(90deg,var(--grad-a),var(--grad-b));color:var(--white);font-size:13px;letter-spacing:1.4px;display:flex;align-items:center;justify-content:center;box-shadow:0 4px 10px rgba(200,110,160,.3);text-decoration:none}
.pill--touch{left:699px;top:3035px;width:140px}
.pill--work{left:708px;top:3092px;width:124px}
.footer-col--connect{left:917px;width:130px;top:2939px}
.social{position:absolute;left:919px;top:3035px;display:flex;gap:8px}
.social span{width:19px;height:19px;border-radius:3px;background:var(--teal)}
</style>
</head>
<body>
<main class="page">
  <section class="band band--projects" aria-label="Projects"></section>
  <div class="projects-panel"></div>
  <h2 class="projects-title">WEB DESIGN BOSTON PROJECTS</h2>

  <div class="project project--roof" role="img" aria-label="Ridgeline Roofing website screenshot with a house photo and mobile view">
    <div class="project__hover">Construction Website Design
      <svg viewBox="0 0 12 18"><path d="M2 2l7 7-7 7" fill="none" stroke="#f06d8f" stroke-width="2.6"/></svg>
    </div>
  </div>
  <div class="project project--builder" role="img" aria-label="Keystone Builders website screenshot with a home exterior photo and mobile view"></div>
  <div class="project project--kitchen" role="img" aria-label="Harborview Kitchen And Bath website screenshot with a kitchen photo and mobile view"></div>
  <div class="project project--music" role="img" aria-label="Little Melodies music education website screenshot with classroom photo and mobile view"></div>
  <div class="project project--legal" role="img" aria-label="Legal recruiting website screenshot with an aerial maze photo and mobile view"></div>
  <div class="project project--billing" role="img" aria-label="Northshore Medical Billing website screenshot with ambulance crew photo and mobile view"></div>

  <div class="carousel-dots"><span class="is-active"></span><span></span><span></span><span></span></div>

  <section class="band band--cta" aria-label="Get started"></section>
  <h2 class="cta-title">Let’s Get Started</h2>
  <p class="cta-sub">READY TO MAKE A REAL CHANGE?<br>LET'S BUILD THIS THING TOGETHER!</p>
  <a class="cta-button" href="#">TELL US ABOUT YOUR PROJECT
    <svg viewBox="0 0 10 16"><path d="M2 2l6 6-6 6" fill="none" stroke="#fff" stroke-width="2.6"/></svg>
  </a>

  <footer>
    <div class="band band--footer"></div>
    <svg class="footer-wave" viewBox="0 0 948 352" preserveAspectRatio="none" aria-hidden="true">
      <path d="M0 90 C60 10 220 -10 380 40 C500 78 560 100 660 40 C760 -20 900 0 948 70 L948 352 L0 352 Z" fill="#d9e5ec"/>
    </svg>

    <div class="footer-col footer-col--start">
      <h3 class="footer-head">READY TO GET<br>STARTED?</h3>
      <p>Ready to start a new project or curious about our process? Drop us a note or give us a call. We are happy to answer any questions and provide a free consultation.</p>
      <div class="footer-phone">
        <svg viewBox="0 0 24 24"><path d="M6.6 10.8a15.1 15.1 0 006.6 6.6l2.2-2.2c.3-.3.7-.4 1-.2 1.1.4 2.3.6 3.6.6.6 0 1 .4 1 1V20c0 .6-.4 1-1 1A17 17 0 013 4c0-.6.4-1 1-1h3.5c.6 0 1 .4 1 1 0 1.3.2 2.5.6 3.6.1.3 0 .7-.2 1z" fill="#2f3a3f"/></svg>
        617-555-0148
      </div>
    </div>

    <div class="footer-col footer-col--brand">
      <div class="brand-name"><i></i>Rise &amp; Reach</div>
      <address>Boston Website Design<br>88 Harbor Ln #210,<br>Boston, MA 02118<br>617-555-0148</address>
    </div>

    <div class="footer-col footer-col--hours">
      <h3 class="footer-head">OPERATING HOURS:</h3>
      <p class="hours">Mon-Sat, 8AM – 8PM</p>
    </div>
    <a class="pill pill--touch" href="#">get in touch</a>
    <a class="pill pill--work" href="#">our work</a>

    <div class="footer-col footer-col--connect">
      <h3 class="footer-head">CONNECT</h3>
    </div>
    <div class="social" aria-label="Social links"><span></span><span></span><span></span><span></span><span></span></div>
  </footer>
</main>
</body>
</html>
```